Business Card For Halvenmoor Financial Consulting

Hi, I would like a business card designed. Bold, modern.
Please use the same design as the logo. I have also attached the website design to see the overall theme.
Wordmark Font
Color: Hex: #01AEF7

```html
<!DOCTYPE html>
<html lang="en">
<head>
<meta charset="utf-8">
<title>Halvenmoor Financial Consulting — Business Card</title>
<link rel="stylesheet" href="https://fonts.googleapis.com/css2?family=Poppins:wght@400;500;600&display=swap">
<style>
  :root {
    --bg: #e6e8ea;
    --card-front: #ffffff;
    --card-back: #16232d;
    --navy: #0b4468;
    --accent: #01aef7;
    --ink: #1a1a1a;
    --rule: #c4c4c4;
    --back-mark: #2f6288;
  }
  * { margin: 0; padding: 0; box-sizing: border-box; }
  html, body { width: 1093px; height: 1200px; overflow: hidden; }
  body {
    background: var(--bg);
    font-family: "Poppins", sans-serif;
    position: relative;
  }
  .card {
    position: absolute;
    left: 265px;
    width: 578px;
    height: 356px;
    border-radius: 26px;
  }
  .card--front { top: 226px; background: var(--card-front); box-shadow: 0 2px 10px rgba(0,0,0,.12); }
  .card--back { top: 621px; background: var(--card-back); }

  .brand { position: absolute; display: flex; align-items: center; }
  .brand__square { background: var(--navy); flex: none; }
  .brand__text { font-weight: 600; color: var(--navy); line-height: 1; }
  .brand__name { display: block; }
  .brand__sub { display: block; }

  .card--front .brand { left: 33px; top: 160px; gap: 10px; }
  .card--front .brand__square { width: 30px; height: 30px; background: var(--accent); }
  .card--front .brand__name { font-size: 26px; letter-spacing: 1px; }
  .card--front .brand__sub { font-size: 8.5px; letter-spacing: 12.2px; margin-top: 6px; }

  .divider {
    position: absolute; left: 289px; top: 74px;
    width: 1px; height: 209px; background: var(--rule);
  }
  .contact { position: absolute; left: 312px; top: 90px; color: var(--ink); }
  .contact__name { font-size: 23px; font-weight: 600; color: var(--navy); line-height: 1.1; letter-spacing: .2px; }
  .contact__title { font-size: 14.5px; color: var(--accent); letter-spacing: .8px; line-height: 1.2; }
  .contact__list { list-style: none; margin-top: 15px; }
  .contact__item { display: flex; align-items: center; gap: 7px; font-size: 17px; line-height: 21px; }
  .contact__item svg { width: 15px; height: 15px; flex: none; }
  .contact__link { color: var(--accent); }
  .contact__address { margin-top: 12px; font-size: 17px; line-height: 21px; }

  .card--back .brand { left: 131px; top: 151px; gap: 14px; }
  .card--back .brand__square { width: 48px; height: 48px; background: var(--back-mark); }
  .card--back .brand__text { color: var(--back-mark); }
  .card--back .brand__name { font-size: 38px; letter-spacing: 1.5px; }
  .card--back .brand__sub { font-size: 12px; letter-spacing: 18.6px; margin-top: 7px; }
</style>
</head>
<body>
  <section class="card card--front" aria-label="Card front">
    <div class="brand">
      <span class="brand__square"></span>
      <span class="brand__text">
        <span class="brand__name">HALVENMOOR</span>
        <span class="brand__sub">CONSULTING</span>
      </span>
    </div>
    <div class="divider"></div>
    <div class="contact">
      <p class="contact__name">MARCUS ELLERY</p>
      <p class="contact__title">MANAGING DIRECTOR</p>
      <ul class="contact__list">
        <li class="contact__item">
          <svg viewBox="0 0 16 16" aria-hidden="true"><path fill="#01aef7" d="M3.5 1.5l2.3 2.8-1.3 1.6c.9 2 2.5 3.6 4.5 4.5l1.6-1.3 2.8 2.3-1.4 2.1C6.5 13.3 2.7 9.5 1.5 3z"/><path fill="none" stroke="#01aef7" stroke-width="1.2" d="M9 3.5a3.5 3.5 0 0 1 3.5 3.5M9 1a6 6 0 0 1 6 6"/></svg>
          <span>044-123 456 789</span>
        </li>
        <li class="contact__item">
          <svg viewBox="0 0 16 16" aria-hidden="true"><rect x="1" y="3" width="14" height="10" fill="#01aef7"/><path fill="none" stroke="#fff" stroke-width="1.2" d="M1 3.5l7 5.5 7-5.5M1 13l5-4.5M15 13l-5-4.5"/></svg>
          <span>info@webname.com</span>
        </li>
        <li class="contact__item">
          <svg viewBox="0 0 16 16" aria-hidden="true"><g fill="none" stroke="#01aef7" stroke-width="1.2"><circle cx="8" cy="8" r="6.5"/><ellipse cx="8" cy="8" rx="3" ry="6.5"/><path d="M1.5 8h13M2.5 4.8h11M2.5 11.2h11"/></g></svg>
          <span>www.<span class="contact__link">websitename</span>.com</span>
        </li>
      </ul>
      <p class="contact__address">421, Address line goes here<br>45452,Country Name</p>
    </div>
  </section>

  <section class="card card--back" aria-label="Card back">
    <div class="brand">
      <span class="brand__square"></span>
      <span class="brand__text">
        <span class="brand__name">HALVENMOOR</span>
        <span class="brand__sub">CONSULTING</span>
      </span>
    </div>
  </section>
</body>
</html>
```